Brightmill Data Works

Our company is about IT hardwares and IT solutions. IT hardware such as PC, RAMS, storage and servers. IT solutions such as project management, BA. We are also selling new technology too.

Target Market(s)

Consumer, Small to Medium Business, Corporate

Requirements
Must have
• The business card must have the following:
• Name:
• Title:
• Contact Number:
• Email address:
• Website:
• Color: Must match the logo color upgrade

```html
<!DOCTYPE html>
<html lang="en">
<head>
<meta charset="utf-8">
<title>Brightmill Data Works – Business Card</title>
<link rel="stylesheet" href="https://fonts.googleapis.com/css2?family=Exo+2:wght@400;600;800&display=swap">
<style>
  :root {
    --bg: #dcdcdc;
    --card-grey: #555657;
    --card-grey-dark: #474849;
    --paper: #f7f7f7;
    --ink-grey: #58595b;
    --orange: #c8782f;
    --orange-light: #de9a4e;
    --white: #ffffff;
  }
  * { margin: 0; padding: 0; box-sizing: border-box; }
  html, body { width: 1200px; height: 864px; overflow: hidden; background: var(--bg); }
  body { position: relative; font-family: "Exo 2", sans-serif; }

  .card {
    position: absolute;
    left: 300px;
    width: 600px;
    height: 343px;
    border-radius: 3px;
    overflow: hidden;
    box-shadow: 0 6px 18px rgba(0,0,0,.18);
  }
  .card--front { top: 48px; background: var(--paper); }
  .card--back {
    top: 473px;
    background: linear-gradient(135deg, var(--card-grey) 0%, var(--card-grey-dark) 100%);
    display: flex; align-items: center; justify-content: center;
  }

  .card__wave { position: absolute; inset: 0; width: 600px; height: 343px; }

  .brand {
    display: flex; flex-direction: column; align-items: center;
    font-weight: 800; text-transform: uppercase; line-height: 1;
  }
  .brand__dot { width: 22px; height: 22px; border-radius: 50%; background: var(--orange); margin-bottom: 12px; }
  .brand__name { font-size: 30px; letter-spacing: 1px; text-align: center; }
  .brand__name span { display: block; }
  .brand__name span + span { font-size: 17px; letter-spacing: 9px; margin-top: 6px; }

  .card--front .brand { position: absolute; left: 110px; top: 30px; width: 300px; color: var(--ink-grey); }
  .card--back .brand { color: var(--white); }
  .card--back .brand__name { font-size: 40px; }
  .card--back .brand__name span + span { font-size: 22px; letter-spacing: 12px; }

  .person { position: absolute; left: 40px; top: 248px; text-transform: uppercase; }
  .person__name { color: var(--white); font-size: 24px; font-weight: 400; letter-spacing: 1px; }
  .person__title { color: var(--orange-light); font-size: 19px; font-weight: 400; letter-spacing: 1px; margin-top: 2px; }

  .contacts { position: absolute; right: 30px; top: 246px; list-style: none; }
  .contacts__item {
    display: flex; align-items: center; justify-content: flex-end; gap: 12px;
    color: var(--white); font-size: 16px; letter-spacing: 1.5px; height: 26px;
  }
  .contacts__icon {
    width: 20px; height: 20px; background: var(--orange);
    display: flex; align-items: center; justify-content: center; flex: none;
  }
  .contacts__icon svg { width: 14px; height: 14px; }
</style>
</head>
<body>

<section class="card card--front" aria-label="Business card front">
  <svg class="card__wave" viewBox="0 0 600 343" aria-hidden="true">
    <defs>
      <linearGradient id="swoosh" x1="0" x2="1">
        <stop offset="0" stop-color="#b9692a"/>
        <stop offset="1" stop-color="#dd9548"/>
      </linearGradient>
    </defs>
    <path d="M0 124 C 120 200, 260 236, 400 228 S 560 206, 600 216 L600 343 L0 343 Z" fill="var(--card-grey)"/>
    <path d="M0 100 C 120 178, 250 216, 390 210 S 550 198, 600 206" fill="none" stroke="url(#swoosh)" stroke-width="6"/>
    <path d="M50 138 C 150 196, 270 226, 400 220 S 560 204, 600 211" fill="none" stroke="url(#swoosh)" stroke-width="3"/>
  </svg>

  <div class="brand">
    <div class="brand__dot"></div>
    <p class="brand__name"><span>Brightmill</span><span>Data Works</span></p>
  </div>

  <div class="person">
    <p class="person__name">Daniel Reyes</p>
    <p class="person__title">Manager</p>
  </div>

  <ul class="contacts">
    <li class="contacts__item">+1-555-014-2368
      <span class="contacts__icon"><svg viewBox="0 0 24 24"><path fill="#fff" d="M6.6 10.8a15 15 0 0 0 6.6 6.6l2.2-2.2c.3-.3.7-.4 1-.2 1.1.4 2.3.6 3.6.6.6 0 1 .4 1 1V20c0 .6-.4 1-1 1A17 17 0 0 1 3 4c0-.6.4-1 1-1h3.5c.6 0 1 .4 1 1 0 1.3.2 2.5.6 3.6.1.3 0 .7-.2 1z"/></svg></span>
    </li>
    <li class="contacts__item">daniel@brightmill.com
      <span class="contacts__icon"><svg viewBox="0 0 24 24"><rect x="3" y="6" width="18" height="12" fill="none" stroke="#fff" stroke-width="2"/><path d="M3 6l9 7 9-7" fill="none" stroke="#fff" stroke-width="2"/></svg></span>
    </li>
    <li class="contacts__item">www.brightmilldata.com
      <span class="contacts__icon"><svg viewBox="0 0 24 24"><g fill="none" stroke="#fff" stroke-width="1.8"><circle cx="12" cy="12" r="9"/><ellipse cx="12" cy="12" rx="4" ry="9"/><path d="M3 12h18M5 7h14M5 17h14"/></g></svg></span>
    </li>
  </ul>
</section>

<section class="card card--back" aria-label="Business card back">
  <div class="brand">
    <div class="brand__dot"></div>
    <p class="brand__name"><span>Brightmill</span><span>Data Works</span></p>
  </div>
</section>

</body>
</html>
```